Flyer für ambulanten Pflegedienst
Zielgruppe
Ambulanter Pflegedienst in Gründung. Habe schon ein Logo und Text. Zielgruppe sind Pflege und Hilfsbedürftige Menschen

```html
<!DOCTYPE html>
<html lang="de">
<head>
<meta charset="utf-8">
<title>Flyer – Pflegewerk Aurin</title>
<link href="https://fonts.googleapis.com/css2?family=Poppins:wght@400;500;600;700&display=swap" rel="stylesheet">
<style>
  :root{
    --teal:#4dbdb5;
    --teal-dark:#3aa8a1;
    --blue:#1a9bc4;
    --blue-deep:#1583aa;
    --ink:#1f1f1f;
    --paper:#fbfbfb;
    --backdrop:#d6d6d6;
  }
  *{box-sizing:border-box;margin:0;padding:0}
  html,body{width:1200px;height:1117px;overflow:hidden}
  body{background:var(--backdrop);font-family:"Poppins",sans-serif;color:var(--ink);position:relative}
  .page{position:absolute;top:182px;width:530px;height:752px;background:var(--paper);overflow:hidden;box-shadow:0 4px 14px rgba(0,0,0,.18)}
  .page--front{left:57px}
  .page--back{left:613px}
  .page__waves{position:absolute;inset:0;width:530px;height:752px}
  .block{position:absolute;font-size:8.6px;line-height:10.7px}
  .block p{margin-bottom:8px}
  .block ul{list-style:none;margin-top:8px}
  .block li{padding-left:10px;position:relative}
  .block li::before{content:"•";position:absolute;left:0;color:var(--ink)}
  .block--back li::before{color:var(--teal)}
  .intro{left:54px;top:133px;width:422px;text-align:center}
  .intro p{margin-bottom:10.7px}
  .pill{display:block;background:var(--teal);color:#fff;font-weight:600;font-size:11px;line-height:17px;text-align:center;border-radius:9px;margin-bottom:6px}
  .brand{position:absolute;left:134px;top:40px;display:flex;align-items:center;gap:10px;color:var(--teal-dark);font-weight:600}
  .brand__dot{width:52px;height:52px;border-radius:50%;background:var(--teal)}
  .brand__name{font-size:28px;line-height:30px}
  .brand__sub{font-size:8px;line-height:11px;letter-spacing:.3px}
  .photo{position:absolute;left:292px;top:523px;width:182px;height:182px;border-radius:50%;border:7px solid var(--teal);background:radial-gradient(circle at 45% 45%,#f1e2d6,#c9b3a5 60%,#9e8c86);}
  .heading{color:var(--teal);font-weight:600;font-size:10.8px;line-height:12.6px;margin-bottom:3px}
  .heading--blue{color:var(--blue)}
  .inline-list{display:flex;gap:14px}
  .cols{display:flex;gap:18px}
  .divider{position:absolute;left:69px;top:383px;width:408px;height:1px;background:var(--blue)}
</style>
</head>
<body>

<section class="page page--front">
  <svg class="page__waves" viewBox="0 0 530 752" aria-hidden="true">
    <path d="M0 0H530V6C420 30 300 12 190 14C110 16 40 32 0 48Z" fill="var(--teal)"/>
    <path d="M0 48C40 32 110 16 190 14C120 22 50 50 0 90Z" fill="var(--blue)"/>
    <path d="M0 720C140 690 300 708 530 690V752H0Z" fill="var(--blue)"/>
    <path d="M0 705C150 676 320 694 530 672V690C300 708 140 690 0 720Z" fill="var(--teal)"/>
    <path d="M270 690C300 720 360 730 420 705L460 700C420 745 330 748 270 715Z" fill="var(--blue-deep)"/>
  </svg>

  <div class="brand">
    <span class="brand__dot"></span>
    <div>
      <div class="brand__name">Pflegewerk Aurin</div>
      <div class="brand__sub">ambulanter Pflegedienst Halvorsen UG<br>Haftungsbeschränkt</div>
    </div>
  </div>

  <div class="block intro">
    <p>Uns liegt es am Herzen durch qualitativ hochwertige und individuelle Unterstützungsleistungen den Menschen ein selbstbestimmtes Leben zu ermöglichen. Wir setzen auf Fachkompetenz und Empathie, um sicherzustellen, dass unsere Kunden die bestmögliche medizinische Versorgung erhalten.</p>
    <p>Unsere Dienstleistung umfasst die ambulante Pflege gemäß SGB XI sowie die Behandlungspflege gemäß SGB V. Betreuungs- und Entlastungszeiten nach § 45 SGB XI um Menschen im Alltag zu unterstützen und ihre Lebensqualität zu steigern.</p>
    <p>Pflegebedürftig ist, wer aufgrund einer körperlichen, geistigen oder seelischen Krankheit bzw. Behinderung in erheblichen Umfang Hilfe bis hin zur vollumfänglichen Betreuung benötigt. Die Leistungen des Altenpflege- und Seniorenbetreuungsdienstes erstrecken sich auf die <strong>Grundpflege, Behandlungspflege, 24-Stundenpflege,</strong></p>
  </div>

  <div class="block" style="left:53px;top:293px;width:184px">
    <span class="pill">Grundpflege</span>
    <p>In der Grundpflege werden die Pflegepersonenin der Verrichtung alltäglicher Grundverrichtungen unterstützt, z.B.</p>
    <ul>
      <li>Duschen</li><li>Baden</li><li>Zahnpflege Kämmen</li><li>Rasieren</li><li>An- und Auskleiden</li><li>Hilfsmittelversorgung</li><li>Mobilisation</li><li>Prophylaxen</li><li>Nahrungsaufnahme</li><li>Toilettengang u.s.w.</li>
    </ul>
  </div>

  <div class="block" style="left:268px;top:293px;width:212px">
    <span class="pill">Behandlungspflege</span>
    <p>Die Behandlungspflege umfasst alle Pflegedienste, die auf ärztlicher Verordnung hin vom Pflegepersonal durchgeführt werden, z. B.</p>
    <ul>
      <li>Pulsmessung</li><li>Blutdruckmessung</li><li>Blutzuckermessung</li><li>Wundversorgung</li><li>Verbandswechsel</li><li>Injektionen (z.b. Insulin)</li><li>Stellen der Medikamente</li><li>Anlegen von Kompressionsverbänden</li><li>An- und Ausziehen von Kompressionsstrümpfen u.s.w.</li>
    </ul>
  </div>

  <div class="block" style="left:53px;top:505px;width:192px">
    <span class="pill">24-Stunden Pflege</span>
    <p>In verschiedenen Situationen ist die stundenweise Pflege nicht ausreichend, z.B. in der Folgezeit eines Krankenhausaufenthaltes. Es wird eine 24-Stunden-Pflege angeboten, im Rahmen derer das Pflegepersonal rund um die Uhr erreichbar ist. Typische Leistungen sind:</p>
    <ul>
      <li>Überwachung der Vitalsituation des Patienten</li><li>Verabreichung von Medikamenten</li><li>Wundversorgung</li><li>Verbandswechsel</li><li>Katheter Versorgung u.s.w.</li>
    </ul>
  </div>

  <div class="photo" role="img" aria-label="Foto: lächelnde Seniorin mit junger Pflegekraft"></div>
</section>

<section class="page page--back">
  <svg class="page__waves" viewBox="0 0 530 752" aria-hidden="true">
    <path d="M0 0H530V6C420 30 300 12 190 14C110 16 40 32 0 48Z" fill="var(--teal)"/>
    <path d="M0 48C40 32 110 16 190 14C120 22 50 50 0 90Z" fill="var(--blue)"/>
    <path d="M0 715C140 685 320 712 530 690V752H0Z" fill="var(--blue)"/>
    <path d="M0 700C150 670 330 698 530 676V690C320 712 140 685 0 715Z" fill="var(--teal)"/>
  </svg>

  <div class="block block--back" style="left:56px;top:43px;width:200px">
    <div class="heading" style="padding-left:27px">Hauswirtschaftliche<br>Versorgung</div>
    <p>In der hauswirtschaftlichen Versorgung werden sämtliche hauswirtschaftlichen Tätigkeiten übernommen, z.B.</p>
    <ul>
      <li>Einkaufen</li><li>Besorgungen</li><li>Zubereitung von Mahlzeiten</li><li>Abwaschen Wäsche waschen</li><li>Bügeln</li><li>Reinigungsarbeiten (Aufräumen, Toilette, Bad, Küche, Wohn- und Schlafbereich, Staubsaugen, Staubwischen)</li><li>Betreuung von Haustieren</li><li>Heizen der Wohnung (Holz, Kohle, Öl)</li><li>Fahrdienste</li>
    </ul>
  </div>

  <div class="block block--back" style="left:56px;top:256px;width:200px">
    <div class="heading heading--blue">Verhinderungspflege</div>
    <p>Das Angebot im Bereich Verhinderungspflege richtet sich an die Angehörigen, die bei der Pflege eine stundenweise Entlastung benötigen. Typische Anlässe sind z.B.</p>
    <ul class="inline-list"><li>Urlaub</li><li>Krankheit</li><li>Überlastung</li></ul>
  </div>

  <div class="block block--back" style="left:272px;top:43px;width:205px">
    <div class="heading heading--blue">Betreuungs- und Entlastungsleistungen nach § 45 SGB XI</div>
    <p>Voraussetzung ist das Vorliegen eines Pflegegrades. Bei der Antragstellung eines Pflegegrades sind wir behilflich und begleiten die Begutachtung durch den Medizinischen Dienst der Krankenkassen.</p>
    <ul>
      <li>Unterstützung bei der Haushaltsführung</li><li>Einkaufen</li><li>Begleitung zu Ärzten</li><li>Arzttermine vereinbaren</li><li>Unterstützung beim Ausfüllen von Formularen und Anträgen</li><li>Spaziergänge</li>
    </ul>
  </div>

  <div class="block block--back" style="left:272px;top:235px;width:210px">
    <div class="heading heading--blue">Alltagsbegleitung</div>
    <p>In der Alltagsbegleitung werden die Pflegepersonen in allen alltäglichen Tätigkeiten und Freizeitaktivitäten unterstützt und begleitet. Typische Leistungen sind z.B.</p>
    <div class="cols">
      <ul><li>Arztbesuche</li><li>Behördengänge</li><li>Kulturelle Veranstaltungen</li><li>Spaziergänge</li><li>Ausflüge</li></ul>
      <ul><li>Wanderungen</li><li>Stadtbummel</li><li>Restaurantbesuche</li><li>Friseurbesuche</li><li>Gedächtnistraining u.s.w.</li></ul>
    </div>
  </div>

  <div class="divider"></div>

  <div class="block" style="left:54px;top:400px;width:410px">
    <p>Der Altenpflege- und Seniorenbetreuungsdienst führt sämtliche Pflegeleistungen kompetent, professionell und zuverlässig aus. Das oberste Ziel der Pflege ist die Sicherung und Verbesserung der Lebensqualität und das Bewahren des gewohnten Lebensumfelds der Pflegepersonen. Krankenhaus- und Betreuungsheimaufenthalte sollen möglichst vermieden werden. Diesem Grundgedanken liegt die Erkenntnis zu Grunde, dass in einer vertrauten Umgebung Kranke oft schneller gesünder werden und gerade ältere Menschen sich zu. Hause besonders wohl und geborgen fühlen.</p>
    <p>Der grundlegende Geschäftsprozess des Unternehmens gliedert sich in die Bereiche Beratung, Pflegekonzept, Vertragsabschluss und Pflege:</p>
  </div>

  <div class="block" style="left:54px;top:518px;width:195px">
    <div class="heading">Beratung</div>
    <p>Kunden werden ausführlich unter Berücksichtigung ihrer Wünsche und Vorstellungen beraten. Denn das vorhandene Pflegeangebot bietet eine Vielzahl an Möglichkeiten. Wichtig ist der Aufbau von Vertrauen.</p>
    <div class="heading" style="margin-top:8px">Pflegekonzept</div>
    <p>Unter Berücksichtigung aller Möglichkeiten und Patientenwünsche wird ein individuelles Leistungskonzept entwickelt und eine verbindliche Kostenaufstellung erstellt.</p>
  </div>

  <div class="block" style="left:269px;top:518px;width:212px">
    <div class="heading">Vertragsschluss</div>
    <p>Alle Aufträge mit Kunden werden in schriftlicher Form geschlossen und beidseitig unterzeichnet.</p>
    <div class="heading" style="margin-top:10px">Pflege</div>
    <p>Die vereinbarten Pflegeleistungen werden nun umgesetzt. Dabei kann der Kunde stets eine hohe Ausführungsqualität erwarten. Es wird für jeden Kunden eine Mappe zur Pflegedokumentation geführt (Pflegesoftware, die stets vom Kunden sowie seinen Angehörigen eingesehen werden kann).</p>
  </div>
</section>

</body>
</html>
```